Non fiction book cover. The book advises how to get a new job.

The book size will be 20cm high by 13cm wide and I need a front cover which can wrap around to the back. This book has a serious message, but I've tried to make it quite light to read and accessible. So I don't want a cover that is too dour or serious and not frivolous either. At the end of the project, I will need a high resolution 3D image of the book, included as part of the package.<br/>The Title of the book is:- "Past Sixty? Hunting for your final post?<br/>by Gareth Millbrook-Ashdown".<br/>I am thinking of a light yellow background, with a striking image to attract attention. The image and words should be clear and sharp.<br/>Here is the, BACK COVER wording.<br/>"This book tells you clearly and simply the steps that you need to take, to get a job, once you’re over 50.<br/>It advises you on the techniques to use to write a killer CV.<br/>It explains how to ensure that your CV attention.<br/>It shows the best way to approach your local job agency.<br/>It demonstrates the best way to use your network.<br/><br/>This book, written by someone with 30 years’ experience in the recruitment industry, gives you ALL the answers.<br/>Whether you are a top executive or someone after some local part time work, then this book is for you. <br/>With the help of this book you will secure your next position.<br/>

Target Market(s)

UK, over 50s, male and female.

Font styles to use
Serif

Colors
fbee3e

Requirements
Must have
• A clear uncluttered cover.
Should not have
• Fussy and over complicated

```html
<!DOCTYPE html>
<html lang="en">
<head>
<meta charset="utf-8">
<title>Past Sixty? — Book Cover Wrap</title>
<link rel="stylesheet" href="https://fonts.googleapis.com/css2?family=EB+Garamond:wght@400;500;700;800&display=swap">
<style>
  :root {
    --cover-yellow: #fbee3e;
    --ink: #111111;
    --rule: #2a2a2e;
    --art-tone: #e9dc3a;
    --backdrop: #ececec;
    --serif: "EB Garamond", Garamond, "Times New Roman", serif;
  }
  * { box-sizing: border-box; margin: 0; padding: 0; }
  html, body {
    width: 1200px; height: 1000px; overflow: hidden;
    background: var(--backdrop);
    font-family: var(--serif);
    color: var(--ink);
  }
  .cover-wrap {
    position: absolute; left: 50px; top: 107px;
    width: 1100px; height: 786px;
    background: var(--cover-yellow);
    display: grid;
    grid-template-columns: 510px 80px 510px;
  }
  .base-rule {
    position: absolute; left: 0; right: 0; top: 700px;
    height: 4px; background: var(--rule);
  }

  /* Back cover */
  .back-cover { position: relative; padding: 44px 40px 0 44px; }
  .back-title {
    text-align: center; font-weight: 700;
    font-size: 44px; line-height: 1; letter-spacing: -0.5px;
  }
  .back-subtitle {
    text-align: center; font-size: 17px; margin-top: 2px;
  }
  .back-blurb {
    margin-top: 30px; font-size: 15.5px; line-height: 1.3;
    text-align: justify; hyphens: auto;
  }

  /* Spine */
  .spine {
    position: relative;
    display: flex; flex-direction: column; align-items: center;
    padding-top: 40px;
  }
  .spine-title, .spine-author {
    writing-mode: vertical-rl;
    white-space: nowrap; font-size: 17px;
  }
  .spine-title { font-weight: 500; letter-spacing: 0.3px; }
  .spine-title strong { font-weight: 800; }
  .spine-author {
    margin-top: 34px; font-variant: small-caps; font-weight: 600;
    letter-spacing: 0.5px;
  }

  /* Front cover */
  .front-cover { position: relative; }
  .front-title {
    position: absolute; left: 0; right: 0; top: 32px;
    text-align: center; font-weight: 800; line-height: 0.86;
    letter-spacing: -2px;
  }
  .front-title .line-one { display: block; font-size: 112px; }
  .front-title .line-two { display: block; font-size: 122px; }
  .front-subtitle {
    position: absolute; left: 0; right: 0; top: 268px;
    text-align: center; font-size: 27px;
  }
  .hourglass-art {
    position: absolute; left: 150px; top: 328px;
    width: 290px; height: 372px;
    background: var(--art-tone);
    border-radius: 14px 14px 0 0;
  }
  .front-author {
    position: absolute; left: 0; right: 0; top: 724px;
    text-align: center; font-size: 30px; font-weight: 600;
    font-variant: small-caps; letter-spacing: 0.5px;
  }
</style>
</head>
<body>
  <main class="cover-wrap">
    <section class="back-cover">
      <h2 class="back-title">PAST SIXTY?</h2>
      <p class="back-subtitle">Hunting for your final post?</p>
      <p class="back-blurb">This book tells you clearly and simply the steps that you need to take, to get a job, once you’re over 50. It advises you on the techniques to use to write a killer CV. It explains how to ensure that your CV attention. It shows the best way to approach your local job agency. It demonstrates the best way to use your network. This book, written by someone with 30 years’ experience in the recruitment industry, gives you ALL the answers. Whether you are a top executive or someone after some local part time work, then this book is for you. With the help of this book you will secure your next position.</p>
    </section>

    <section class="spine">
      <p class="spine-title"><strong>PAST SIXTY?</strong> HUNTING FOR YOUR FINAL POST?</p>
      <p class="spine-author">Gareth Millbrook-Ashdown</p>
    </section>

    <section class="front-cover">
      <h1 class="front-title">
        <span class="line-one">PAST</span>
        <span class="line-two">SIXTY?</span>
      </h1>
      <p class="front-subtitle">Hunting for your final post?</p>
      <div class="hourglass-art" role="img" aria-label="Outline drawing of an hourglass with sand running low, standing on the cover's base line"></div>
      <p class="front-author">Gareth Millbrook-Ashdown</p>
    </section>

    <div class="base-rule"></div>
  </main>
</body>
</html>
```